Trailhead Cove Website - Sell Outdoor product

We are a mom and pop company that just opened our website.

We need a fresh, professional, and nice looking website for our outdoor products. We sell hunting, camping, fishing, and hiking products/accessories to name a few. Some of these products are optics, gun safes, gun bi-pods and tripods, gun lights, hunting camera, tents, hearing protection, targets, fishing poles, and hiking backpacks to name a few.

Our current website is: http://www.trailheadcove-example.com . You'll see our logo on the website, and it is attached. We aren't married to this logo, so if the designer thinks they can modify it or even come up with a better design for the website, they are more than welcome to do so. We need someone with good images of their own (clip art and/or outdoor images) they can use if they need to for our website.

I also attached a idea I had in plandraw, but please don't think this is set in stone. It is just a very rough idea. You can also go to our bazarro site to see what we sell: www.bazarro-example.com/shops/k9qz311mrtxn4p . Right now we sell everything on Bazarro, but our website will just focus on outdoor product. So please make it an outdoor focused website. And you can be creative with some of the product category names. We also want to leave room for some parallel product in the future. Like garden tools, back yard furniture, and BBQs.

Our company also wants to include a deals section on the website. We will probably update it once a week or month. I have included what I did for a deal and accompanying images for it. Image is called Morvelid (And the main images are 01 and 02).

We also want to make sure the file is compatible with our current web-hosting company, https://www.hostlyne-example.com. So I included a webpage layout zip folder. If you have any questions, please contact me.

This is for a PSD and HTML/CSS webpage. If you have any artwork or images that you own and want to use them for the webpage, please do so.

Target Market(s)

The hunter, outdoors person, camper, hiker, and etc.

Industry/Entity Type

It Company

Coding

Coded - Design and coding required

Number of Pages Required

3 page

Requirements
Must have
• The main page. PSD and HTML/CSS file.
• The category page. PSD and HTML/CSS file
• The product display page. PSD and HTML/CSS file
• Please also use some images that you have or from the sites below:
• You can get free stock images for 7 days (20 per day) from this site:
• https://www.pixelvault-example.com/complimentary/PVXTRL/?utm_source=PVXTrialFT&utm_medium=cpc&utm_campaign=PVXTrialFT&gclid=QWRt5mnBkdTRZpLoWsePb7uVbQ
• Has 14 good sites:
• http://www.venturedesk-example.com/article/517293
• Here are the ones I like:
• https://clearshot-example.com/
• http://brightwide-example.com/
• http://www.sitebloom-example.com/free/nature
• http://www.pictorium-example.com/archive
• http://tinyframes-example.co/
• http://old.vintlens-example.co/search/hiking
• http://fetchpix.blogsite-example.com/
• http://rolvenpask-example.com/post/584920173645/download
• http://openimagevault-example.com/
• If there is a photographer listed on or next to the image, on the bottom lower corner of the image, please put the photographer's name.
Nice to have
• I would like to have an unsubscribe page. If the designer has any of their own images of the outdoor world, and they want to use them, please do. Just make the right graphic changes to make it look good.
Should not have
• Try and keep green color to a minimum.

```html
<!DOCTYPE html>
<html lang="en">
<head>
<meta charset="utf-8">
<title>Trailhead Cove – Outdoor Store</title>
<link href="https://fonts.googleapis.com/css2?family=Open+Sans:wght@400;600;700;800&family=Fira+Sans:wght@700;800&family=Dancing+Script:wght@500&display=swap" rel="stylesheet">
<style>
:root{
  --yellow:#efb00f;
  --yellow-dark:#d9a210;
  --yellow-line:#e6ab12;
  --brown:#7a5200;
  --ink:#111;
  --text:#2b2b2b;
  --teal:#3b8f79;
  --red:#b51f2e;
  --gold:#d4a01e;
  --footer:#1f1f1f;
  --footer-bottom:#181818;
  --footer-text:#9a9a9a;
}
*{margin:0;padding:0;box-sizing:border-box}
html,body{width:1137px;height:1200px;overflow:hidden;background:#fff}
body{position:relative;font-family:"Open Sans",sans-serif;color:var(--text)}
.sidebar{position:absolute;left:0;top:0;width:234px;height:1043px;background:var(--yellow)}
.brand{height:120px;display:flex;align-items:center;justify-content:center;gap:8px}
.brand-mark{width:14px;height:14px;background:var(--ink)}
.brand-name{font-weight:800;font-size:19px;color:var(--ink);letter-spacing:.5px;text-transform:uppercase}
.category-menu{list-style:none}
.category-menu li{height:53.6px;background:var(--yellow-dark);border-bottom:1px solid var(--yellow-line);display:flex;align-items:center;justify-content:space-between;padding:0 19px 0 20px;color:#fff;font-size:12px;text-transform:uppercase}
.category-menu li svg{width:7px;height:10px}
.about{padding:34px 20px 0 20px}
.about h2{font-size:16px;font-weight:700;line-height:1.4;color:var(--ink);text-transform:uppercase}
.about h2 span{color:#fff;display:block}
.about p{margin-top:13px;font-size:10.5px;line-height:20.3px;color:var(--brown)}
.social{position:absolute;left:20px;top:910px}
.social h2{font-size:15.5px;font-weight:700;line-height:1.4;color:var(--ink);text-transform:uppercase}
.social h2 span{color:#fff;display:block}
.social-list{display:flex;gap:8px;margin-top:12px;margin-left:3px}
.social-list span{width:27px;height:27px;border-radius:50%;background:var(--ink)}
.topbar{position:absolute;left:234px;top:0;width:903px;height:85px}
.tagline{position:absolute;left:24px;top:30px;font-family:"Dancing Script",cursive;font-size:17px;color:#333}
.newsletter-btn{position:absolute;left:280px;top:28px;width:159px;height:33px;background:var(--teal);color:#fff;font-size:10px;display:flex;align-items:center;justify-content:center;text-transform:uppercase}
.account-links{position:absolute;top:39px;font-size:10px;color:#444;text-transform:uppercase}
.account{left:577px}.login{left:689px}
.cart{position:absolute;left:747px;top:33px;display:flex;align-items:center;gap:9px;font-size:10px;color:#444;text-transform:uppercase}
.main-nav{position:absolute;left:234px;top:85px;width:903px;height:35px;background:var(--ink)}
.main-nav a{position:absolute;top:11px;color:#fff;font-size:10px;font-weight:600;text-decoration:none;text-transform:uppercase}
.hero{position:absolute;left:250px;top:138px;width:872px;height:405px;overflow:hidden}
.hero-photo{position:absolute;inset:0;background:linear-gradient(100deg,#dfe1e3 0%,#cfd2d4 45%,#7f7a72 65%,#4a4642 80%,#8c8780 100%)}
.hero-brand{position:absolute;left:74px;top:108px;display:flex;align-items:center;gap:12px}
.hero-brand span.sq{width:26px;height:26px;background:var(--ink)}
.hero-brand span.name{font-family:"Fira Sans",sans-serif;font-weight:800;font-size:50px;color:var(--ink);text-transform:uppercase}
.hero-kicker{position:absolute;left:62px;top:207px;font-family:"Fira Sans",sans-serif;font-weight:800;font-size:35px;color:var(--teal);letter-spacing:.5px}
.hero-year{position:absolute;left:60px;top:245px;font-family:"Fira Sans",sans-serif;font-weight:800;font-size:86px;line-height:1;color:var(--red)}
.hero-line1{position:absolute;left:285px;top:260px;font-family:"Fira Sans",sans-serif;font-weight:800;font-size:31px;color:var(--gold)}
.hero-line2{position:absolute;left:285px;top:297px;font-family:"Fira Sans",sans-serif;font-weight:800;font-size:31px;color:var(--ink)}
.hero-arrows{position:absolute;left:812px;top:370px;display:flex;gap:1px}
.hero-arrows span{width:23px;height:23px;background:var(--red);display:flex;align-items:center;justify-content:center}
.new-products h1{position:absolute;left:257px;top:571px;font-size:15.5px;font-weight:700;color:var(--ink);text-transform:uppercase}
.product{position:absolute;width:205px}
.product .shot{width:205px;height:145px}
.product h3{margin-top:12px;font-size:11px;font-weight:700;color:#333;text-transform:uppercase}
.footer{position:absolute;left:0;top:1043px;width:1137px;height:157px;background:var(--footer)}
.footer-links{position:absolute;left:39px;font-size:10.5px;color:var(--footer-text);word-spacing:0}
.footer-links span.sep{margin:0 22px}
.help{position:absolute;left:938px;top:35px;display:flex;align-items:center;gap:16px}
.help-icon{width:42px;height:42px;background:var(--yellow);display:flex;align-items:center;justify-content:center}
.help-text{color:#8c8c8c;font-size:14px;line-height:21px}
.help-text strong{display:block;color:#b9b9b9;font-size:16px;font-weight:700}
.footer-bottom{position:absolute;left:0;bottom:0;width:100%;height:44px;background:var(--footer-bottom);display:flex;align-items:center;justify-content:center;font-size:10.5px;color:#8c8c8c}
</style>
</head>
<body>
<aside class="sidebar">
  <div class="brand"><span class="brand-mark"></span><span class="brand-name">Trailhead Cove</span></div>
  <ul class="category-menu">
    <li>Optics<svg viewBox="0 0 7 10"><path d="M1 1l4 4-4 4" fill="none" stroke="#fff" stroke-width="1.4"/></svg></li>
    <li>Safes<svg viewBox="0 0 7 10"><path d="M1 1l4 4-4 4" fill="none" stroke="#fff" stroke-width="1.4"/></svg></li>
    <li>Bipod and Tripods<svg viewBox="0 0 7 10"><path d="M1 1l4 4-4 4" fill="none" stroke="#fff" stroke-width="1.4"/></svg></li>
    <li>Lights<svg viewBox="0 0 7 10"><path d="M1 1l4 4-4 4" fill="none" stroke="#fff" stroke-width="1.4"/></svg></li>
    <li>Cameras<svg viewBox="0 0 7 10"><path d="M1 1l4 4-4 4" fill="none" stroke="#fff" stroke-width="1.4"/></svg></li>
    <li>Tents<svg viewBox="0 0 7 10"><path d="M1 1l4 4-4 4" fill="none" stroke="#fff" stroke-width="1.4"/></svg></li>
    <li>Ear Protection<svg viewBox="0 0 7 10"><path d="M1 1l4 4-4 4" fill="none" stroke="#fff" stroke-width="1.4"/></svg></li>
    <li>Targets<svg viewBox="0 0 7 10"><path d="M1 1l4 4-4 4" fill="none" stroke="#fff" stroke-width="1.4"/></svg></li>
  </ul>
  <section class="about">
    <h2>About<span>Trailhead Cove</span></h2>
    <p>Simply dummy text of the printing and typesetting industry. Lorem Ipsum has been the industry's standard dummy text ever since the 1500s, when an unknown printer took a galley of type and scrambled it to make a type specimen book...</p>
  </section>
  <section class="social">
    <h2>Connect with<span>our social network</span></h2>
    <div class="social-list" aria-label="Social network links"><span></span><span></span><span></span><span></span><span></span></div>
  </section>
</aside>

<header class="topbar">
  <p class="tagline">Get our recent updates through your email id</p>
  <a class="newsletter-btn">Join our newsletter</a>
  <span class="account-links account">My Account</span>
  <span class="account-links login">Login</span>
  <span class="cart"><svg width="18" height="22" viewBox="0 0 18 22"><rect x="1" y="7" width="16" height="14" fill="none" stroke="#888" stroke-width="1.2"/><path d="M5 9V5a4 4 0 0 1 8 0v4" fill="none" stroke="#888" stroke-width="1.2"/></svg>Your cart is : 0 items</span>
</header>

<nav class="main-nav">
  <a style="left:27px">Home</a>
  <a style="left:121px">Huntingaccessories</a>
  <a style="left:294px">Camping</a>
  <a style="left:403px">Fishing</a>
  <a style="left:507px">Hiking</a>
  <a style="left:605px">This weeksdeals</a>
  <a style="left:757px">Brands</a>
</nav>

<section class="hero">
  <div class="hero-photo" role="img" aria-label="Hiker with a large backpack looking through binoculars against misty mountains"></div>
  <div class="hero-brand"><span class="sq"></span><span class="name">Trailhead Cove</span></div>
  <div class="hero-kicker">EXCLUSIVE PRODUCTS</div>
  <div class="hero-year">2015</div>
  <div class="hero-line1">NEW ARRAIVELS</div>
  <div class="hero-line2">SHOP ONLINE</div>
  <div class="hero-arrows">
    <span><svg width="7" height="11" viewBox="0 0 7 11"><path d="M6 1L1.5 5.5 6 10" fill="none" stroke="#fff" stroke-width="1.2"/></svg></span>
    <span><svg width="7" height="11" viewBox="0 0 7 11"><path d="M1 1l4.5 4.5L1 10" fill="none" stroke="#fff" stroke-width="1.2"/></svg></span>
  </div>
</section>

<section class="new-products">
  <h1>New Products</h1>
  <div class="product" style="left:257px;top:615px"><div class="shot" role="img" aria-label="Cyclist wearing a helmet and sunglasses under a blue sky" style="background:linear-gradient(135deg,#4f8ed6,#b9cde6 60%,#6b6f74)"></div><h3>Sunglass, W/Exchange Lens</h3></div>
  <div class="product" style="left:477px;top:615px"><div class="shot" role="img" aria-label="Close-up of a black camera body" style="background:linear-gradient(135deg,#d4d4d4,#5a5a5a 55%,#1a1a1a)"></div><h3>Camera</h3></div>
  <div class="product" style="left:696px;top:615px"><div class="shot" role="img" aria-label="Hiker with backpack raising arms toward the sky" style="background:linear-gradient(160deg,#9fb7c4,#e5d8c3 55%,#8a7a66)"></div><h3>Trucking Bags</h3></div>
  <div class="product" style="left:915px;top:615px"><div class="shot" role="img" aria-label="Black over-ear headphones with coiled cable" style="background:linear-gradient(135deg,#cfcfcf,#3b3b3b 55%,#0f0f0f)"></div><h3>Head Phones</h3></div>
  <div class="product" style="left:257px;top:823px"><div class="shot" role="img" aria-label="Orange tent pitched in a green forest" style="background:linear-gradient(160deg,#2f4a2a,#4f7a3a 50%,#e0652a 75%,#3f6a2d)"></div><h3>Person Tent</h3></div>
  <div class="product" style="left:477px;top:823px"><div class="shot" role="img" aria-label="Black engraved pen with a bullet-shaped tip" style="background:linear-gradient(160deg,#1a1a1a,#3a3a3a 40%,#f2f2f2 70%,#ffffff)"></div><h3>Morvelid</h3></div>
  <div class="product" style="left:696px;top:823px"><div class="shot" role="img" aria-label="Cyclist wearing a sports watch gripping handlebars" style="background:linear-gradient(135deg,#f3efe8,#8a5a3c 45%,#26262e 75%,#c9302c)"></div><h3>Watches</h3></div>
  <div class="product" style="left:915px;top:823px"><div class="shot" role="img" aria-label="Gold fishing reel against a blue sky" style="background:linear-gradient(135deg,#3d7bd6,#9dbbe6 45%,#d6a334 70%,#4a4a4a)"></div><h3>Fishing</h3></div>
</section>

<footer class="footer">
  <p class="footer-links" style="top:35px">About US<span class="sep">/</span>Terms &amp; Conditions<span class="sep">/</span>Contact Us<span class="sep">/</span>Contact Us<span class="sep">/</span>Shipping and Return</p>
  <p class="footer-links" style="top:64px">Home<span class="sep">/</span>About US<span class="sep">/</span>FAQ<span class="sep">/</span>Blog<span class="sep">/</span>Join Our Newsletter<span class="sep">/</span>Privacy</p>
  <div class="help">
    <div class="help-icon"><svg width="20" height="20" viewBox="0 0 24 24"><path d="M6.6 10.8a15.1 15.1 0 0 0 6.6 6.6l2.2-2.2a1 1 0 0 1 1-.25 11.4 11.4 0 0 0 3.6.57 1 1 0 0 1 1 1V20a1 1 0 0 1-1 1A17 17 0 0 1 3 4a1 1 0 0 1 1-1h3.5a1 1 0 0 1 1 1c0 1.25.2 2.45.57 3.57a1 1 0 0 1-.25 1z" fill="#1f1f1f"/></svg></div>
    <div class="help-text">Need Help:<strong>(555) 014-2290</strong></div>
  </div>
  <div class="footer-bottom">© 2015 Trailhead Cove LLC. All rights reserved</div>
</footer>
</body>
</html>
```